Networking Events Calendar/Diary

We need a responsive website that can act as both an online diary/calendar and a resource for community and networking events similar to brimtolvenquarrix.com (we do not want a clone, but one with similar functionality). We need to be able to host adverts, have a client area for clients to add their own events to the diary. This needs to have the functionality that clients have to pay to add recurring events. Some integration would be useful so that if a clients already has their own online diary on their website then using an API possibly to also add that event into our online diary

Industry/Entity Type

Events

Coding

Coded - Design and coding required

Number of Pages Required

5+ page

Requirements
Must have
• My project must have a calendar area, space for ads, be responsive and easily viewable on mobile. A subscribers area for clients and a way to purchase premium status so that premium events are highlighted.

```html
<!DOCTYPE html>
<html lang="en">
<head>
<meta charset="utf-8">
<title>Quellmar Events</title>
<link href="https://fonts.googleapis.com/css2?family=Exo+2:wght@400;500;600&family=PT+Sans:wght@400;700&display=swap" rel="stylesheet">
<style>
:root{
  --blue:#0b5fcf;
  --blue-dark:#0a4fb0;
  --red:#d9371a;
  --ink:#333;
  --muted:#777;
  --line:#ddd;
  --bg:#f1f1f1;
  --dark:#232426;
  --nav:#1a1a1a;
}
*{box-sizing:border-box;margin:0;padding:0}
html,body{width:1200px;height:2166px;overflow:hidden;background:var(--bg);font-family:"PT Sans",sans-serif;color:var(--ink)}
.page{position:relative;width:1200px;height:2166px;overflow:hidden}
.abs{position:absolute}
.heading{font-family:"Exo 2",sans-serif;font-weight:400;text-transform:uppercase;letter-spacing:.3px;white-space:nowrap}

.topbar{left:0;top:0;width:1200px;height:46px;background:#ececec}
.toplinks{right:222px;top:16px;font-size:11.5px;color:var(--muted)}
.toplinks span{margin:0 6px}
.social{display:flex;gap:5px}
.social i{display:block;width:17px;height:17px;border-radius:2px}
.s1{background:#3b5b99}.s2{background:#28a9e1}.s3{background:#d6432f}.s4{background:#f0892b}

.header{left:0;top:46px;width:1200px;height:84px;background:#fff}
.logo{left:111px;top:24px;font-family:"Exo 2",sans-serif;font-weight:600;font-size:28px;letter-spacing:.5px;color:#1d1d1d;white-space:nowrap}
.logo b{color:var(--blue);font-weight:600}
.search{left:897px;top:19px;width:189px;height:46px;border:1px solid #ddd;font-size:11px;color:#999;padding:15px 14px;background:#fff}
.search svg{position:absolute;right:14px;top:16px}

.nav{left:0;top:130px;width:1200px;height:52px;background:linear-gradient(#2a2a2a,#111)}
.nav ul{position:absolute;left:111px;top:0;display:flex;list-style:none}
.nav li{height:52px;line-height:52px;text-align:center;font-size:12px;color:#eee;border-right:1px solid #333}
.nav li.active{background:var(--blue)}

.hero{left:0;top:182px;width:1200px;height:433px;background:linear-gradient(135deg,#e9eef3 0%,#c9d4de 40%,#8e9fb0 70%,#dfe5ea 100%)}
.caption{left:0;top:536px;width:1200px;height:79px;background:rgba(30,30,30,.72);color:#fff;padding:19px 111px}
.caption h2{font-size:16px;font-weight:700}
.caption p{font-size:11.5px;margin-top:4px;color:#ddd}
.slide-arrows{left:1018px;top:493px;display:flex;gap:2px}
.slide-arrows span{width:34px;height:30px;background:#3a3a3a;display:flex;align-items:center;justify-content:center}

.up-band{left:90px;top:640px;width:1018px;height:70px;background:var(--blue)}
.up-band h3{position:absolute;left:21px;top:21px;font-size:18px;color:#fff}
.up-fold{top:699px}
.up-panel{left:111px;top:699px;width:975px;height:144px;background:#ddd}
.card{top:719px;width:286px;height:100px;background:#f7f7f7;border:1px solid #ccc;padding:23px 18px}
.date{position:absolute;left:18px;top:23px;width:52px;height:54px;background:#252525;color:#fff;text-align:center;border-radius:2px}
.date small{display:block;font-size:10px;margin-top:6px}
.date b{display:block;font-size:24px;font-weight:400;line-height:24px}
.card .info{position:absolute;left:82px;top:22px;font-size:10px;color:#888;white-space:nowrap}
.card .info h4{font-size:14px;font-weight:400;color:var(--red);margin:3px 0 4px}
.card .info .pin{color:#8a9ab0}

.sec-title{font-size:21px;color:#2b2b2b}
.sec-rule{height:3px;background:linear-gradient(90deg,#555 0,#555 28%,var(--blue) 28%,var(--blue) 100%)}
.plus{width:51px;height:43px;background:var(--blue);color:#fff;font-size:24px;font-weight:700;text-align:center;line-height:42px}
.side-title{font-size:15px;color:#2b2b2b}
.side-rule{height:3px;background:#555}

.thumb{border-radius:1px}
.meta{font-size:10px;color:#888;display:flex;gap:12px;white-space:nowrap}
.meta i{font-style:normal;color:var(--red)}
.txt{font-size:13px;line-height:21px;color:#444}
.sep{height:1px;background:var(--line)}

.tr-text{font-size:11.5px;line-height:20px;color:#555;text-align:justify}
.tweet-ico{width:46px;height:46px;background:#2aa3e0;border-radius:2px}
.tweet h5{font-size:11px;color:#2aa3e0;font-weight:400}
.tweet p{font-size:11px;color:#777;line-height:17px}

.footer{left:0;top:1788px;width:1200px;height:296px;background:var(--dark)}
.f-title{font-size:15px;color:#fff;top:1829px}
.f-rule{top:1858px;height:3px;background:#444;width:226px}
.f-small{font-size:11px;line-height:20px;color:#999}
.f-date{font-size:11px;color:#eee}
.f-date i,.f-links i{font-style:normal;color:var(--red)}
.f-links{font-size:11px;color:#ddd;line-height:34px;text-transform:uppercase}
.email{left:872px;top:1939px;width:226px;height:44px;background:#1b1c1e;border:1px solid #3a3a3a;color:#aaa;font-size:11px;padding:14px 16px}
.subscribe{left:956px;top:1995px;width:142px;height:46px;background:var(--blue);border:1px solid #3b82e4;color:#fff;font-weight:700;font-size:15px;text-align:center;line-height:44px;border-radius:2px}
.bottom{left:0;top:2084px;width:1200px;height:82px;background:var(--blue)}
.bottom p{position:absolute;left:120px;top:34px;color:#fff;font-size:11px}
</style>
</head>
<body>
<div class="page">

  <div class="abs topbar"></div>
  <div class="abs toplinks">Login <span>|</span> Contact Us <span>|</span> Tell a Friend <span>|</span> Useful Links</div>
  <div class="abs social" style="left:1000px;top:13px"><i class="s1"></i><i class="s2"></i><i class="s3"></i><i class="s4"></i></div>

  <div class="abs header">
    <div class="abs logo"><b>QUELLMAR</b> EVENTS</div>
    <div class="abs search">Search...
      <svg width="12" height="12" viewBox="0 0 12 12"><circle cx="5" cy="5" r="3.6" fill="none" stroke="#888" stroke-width="1.5"/><line x1="7.6" y1="7.6" x2="11" y2="11" stroke="#888" stroke-width="1.5"/></svg>
    </div>
  </div>

  <nav class="abs nav">
    <ul>
      <li class="active" style="width:91px">Home</li>
      <li style="width:169px">Events by Region</li>
      <li style="width:183px">Events by Town/City</li>
      <li style="width:156px">Business Shows</li>
      <li style="width:95px">Blog</li>
      <li style="width:162px">Event Franchises</li>
      <li style="width:119px;border-right:0">Contact Us</li>
    </ul>
  </nav>

  <div class="abs hero" role="img" aria-label="Business people networking in a bright open office"></div>
  <div class="abs caption">
    <h2>Lorem ipsum dolor sit amet, consectetur adipiscing elit</h2>
    <p>Aliquam in sodales nisl. Suspendisse fermentum dignissim diam, eget sollicitudin tellus lobortis id. In maximus congue nibh, in semper turpis aliquet vitae.</p>
  </div>
  <div class="abs slide-arrows">
    <span><svg width="8" height="10"><path d="M6 1L2 5l4 4" stroke="#fff" stroke-width="1.6" fill="none"/></svg></span>
    <span><svg width="8" height="10"><path d="M2 1l4 4-4 4" stroke="#fff" stroke-width="1.6" fill="none"/></svg></span>
  </div>

  <div class="abs up-panel"></div>
  <svg class="abs up-fold" style="left:90px" width="21" height="11"><path d="M0 0h21v11z" fill="#06409a"/></svg>
  <svg class="abs up-fold" style="left:1087px" width="21" height="11"><path d="M0 0h21L0 11z" fill="#06409a"/></svg>
  <div class="abs up-band">
    <h3 class="heading">Upcoming Events</h3>
    <svg class="abs" style="right:20px;top:27px" width="34" height="15"><circle cx="7" cy="7.5" r="6.5" fill="#fff"/><path d="M8.5 4.5L5.5 7.5l3 3" stroke="#0b5fcf" stroke-width="1.8" fill="none"/><circle cx="26" cy="7.5" r="6.5" fill="#fff"/><path d="M24.5 4.5l3 3-3 3" stroke="#0b5fcf" stroke-width="1.8" fill="none"/></svg>
  </div>

  <div class="abs card" style="left:134px">
    <div class="date"><small>Dec</small><b>14</b></div>
    <div class="info"><span style="color:var(--blue)">&#9719;</span> 6.00 PM - 7.00 PM<h4>Lorem ipsum dolor sit amet</h4><span class="pin">&#9679;</span> Lorem Ipsm, Lorem Ipsm - 123 456</div>
  </div>
  <div class="abs card" style="left:455px">
    <div class="date"><small>Dec</small><b>16</b></div>
    <div class="info"><span style="color:var(--blue)">&#9719;</span> 6.00 PM - 7.00 PM<h4>Aenean a est eget dolor</h4><span class="pin">&#9679;</span> Lorem Ipsm, Lorem Ipsm - 123 456</div>
  </div>
  <div class="abs card" style="left:774px">
    <div class="date"><small>Dec</small><b>18</b></div>
    <div class="info"><span style="color:var(--blue)">&#9719;</span> 6.00 PM - 7.00 PM<h4>Proin sit amet feugiat</h4><span class="pin">&#9679;</span> Lorem Ipsm, Lorem Ipsm - 123 456</div>
  </div>

  <h3 class="abs heading sec-title" style="left:111px;top:872px">Latest Events</h3>
  <div class="abs sec-rule" style="left:111px;top:907px;width:728px"></div>
  <div class="abs plus" style="left:787px;top:867px">+</div>

  <div class="abs thumb" style="left:111px;top:940px;width:309px;height:185px;background:radial-gradient(circle at 55% 20%,#ffe27a 0%,#f08a1c 25%,#7a2a8c 55%,#141430 90%)" role="img" aria-label="Concert crowd under bright stage lights"></div>
  <p class="abs" style="left:111px;top:1142px;width:315px;font-size:14px;font-weight:700;line-height:24px;color:#333">Sed ut elementum justo. Duis et eros eu augue hendrerit dapibus eget vel urna.</p>
  <div class="abs meta" style="left:111px;top:1200px"><span><i>&#9632;</i> Admin</span><span><i>&#9632;</i> November 24, 2015</span><span><i>&#9679;</i> 14</span></div>
  <p class="abs" style="left:111px;top:1240px;width:315px;font-size:11.5px;line-height:24px;color:#888">Etiam ac orci in dui luctus semper. Duis sed lorem finibus, volutpat ex non, bibendum turpis...</p>

  <div class="abs thumb" style="left:446px;top:940px;width:119px;height:82px;background:linear-gradient(#d8d36a,#7fa43a)" role="img" aria-label="Friends in a sunny field"></div>
  <p class="abs txt" style="left:576px;top:939px;width:263px">Etiam ac orci in dui luctus semper. Duis sed lorem finibus, volutpat ex non.</p>
  <div class="abs meta" style="left:576px;top:998px"><span><i>&#9632;</i> Admin</span><span><i>&#9632;</i> November 23, 2015</span><span><i>&#9679;</i> 14</span></div>
  <div class="abs sep" style="left:446px;top:1043px;width:393px"></div>

  <div class="abs thumb" style="left:446px;top:1060px;width:119px;height:82px;background:linear-gradient(#eef2f6,#9aa8b8)" role="img" aria-label="Modern glass office interior"></div>
  <p class="abs txt" style="left:576px;top:1059px;width:263px">Nunc non justo consequat, mattis augue ac, pharetra nulla.</p>
  <div class="abs meta" style="left:576px;top:1118px"><span><i>&#9632;</i> Admin</span><span><i>&#9632;</i> November 22, 2015</span><span><i>&#9679;</i> 14</span></div>
  <div class="abs sep" style="left:446px;top:1164px;width:393px"></div>

  <div class="abs thumb" style="left:446px;top:1183px;width:119px;height:82px;background:linear-gradient(135deg,#2a1f4a,#b0306a,#1a1a30)" role="img" aria-label="Party guests celebrating"></div>
  <p class="abs txt" style="left:576px;top:1182px;width:263px">Nulla eget leo posuere, iaculis orci quis, scelerisque quam.</p>
  <div class="abs meta" style="left:576px;top:1241px"><span><i>&#9632;</i> Admin</span><span><i>&#9632;</i> November 21, 2015</span><span><i>&#9679;</i> 14</span></div>
  <div class="abs sep" style="left:446px;top:1285px;width:393px"></div>

  <h3 class="abs heading sec-title" style="left:111px;top:1330px">Latest Blog</h3>
  <div class="abs sec-rule" style="left:111px;top:1365px;width:728px"></div>
  <div class="abs plus" style="left:787px;top:1325px">+</div>

  <div class="abs thumb" style="left:111px;top:1398px;width:120px;height:82px;background:linear-gradient(135deg,#e7edf3,#8fa3b8)" role="img" aria-label="Business people walking in a lobby"></div>
  <p class="abs txt" style="left:243px;top:1397px;width:221px;text-align:justify">Etiam ac orci in dui luctus semper. Duis sed lorem finibus, volutpat</p>
  <div class="abs meta" style="left:243px;top:1456px"><span><i>&#9632;</i> Admin</span><span><i>&#9632;</i> November 23, 2015</span><span><i>&#9679;</i> 14</span></div>

  <div class="abs thumb" style="left:487px;top:1398px;width:119px;height:82px;background:linear-gradient(135deg,#c9b9a3,#5d6d7e)" role="img" aria-label="Team meeting around laptops"></div>
  <p class="abs txt" style="left:617px;top:1397px;width:221px;text-align:justify">Proin sit amet feugiat sapien. Vestibulum a tortor</p>
  <div class="abs meta" style="left:617px;top:1456px"><span><i>&#9632;</i> Admin</span><span><i>&#9632;</i> November 23, 2015</span><span><i>&#9679;</i> 14</span></div>

  <div class="abs thumb" style="left:111px;top:1518px;width:120px;height:82px;background:linear-gradient(135deg,#eef0f2,#6b7380)" role="img" aria-label="Colleagues at a conference table"></div>
  <p class="abs txt" style="left:243px;top:1517px;width:221px;text-align:justify">Vestibulum bibendum, lectus at tincidunt gravida.</p>
  <div class="abs meta" style="left:243px;top:1576px"><span><i>&#9632;</i> Admin</span><span><i>&#9632;</i> November 23, 2015</span><span><i>&#9679;</i> 14</span></div>

  <div class="abs thumb" style="left:487px;top:1518px;width:119px;height:82px;background:linear-gradient(135deg,#f2f2f2,#9ab0c4)" role="img" aria-label="Laptop showing growth charts"></div>
  <p class="abs txt" style="left:617px;top:1517px;width:221px;text-align:justify">Sed tristique, mi at sagittis molestie, nisi nulla laoreet urna.</p>
  <div class="abs meta" style="left:617px;top:1576px"><span><i>&#9632;</i> Admin</span><span><i>&#9632;</i> November 23, 2015</span><span><i>&#9679;</i> 14</span></div>

  <div class="abs" style="left:111px;top:1661px;width:724px;height:88px;border:2px solid #f0a830;background:linear-gradient(90deg,#ffd65a,#f39a1c 50%,#e9650e)" role="img" aria-label="Advertising banner: Morbi fringilla porta tur, click here"></div>

  <h3 class="abs heading side-title" style="left:862px;top:868px">Trending</h3>
  <div class="abs side-rule" style="left:862px;top:897px;width:225px"></div>

  <div class="abs thumb" style="left:862px;top:921px;width:84px;height:57px;background:linear-gradient(135deg,#e6ecf1,#8e9eb0)" role="img" aria-label="Office networking event"></div>
  <p class="abs tr-text" style="left:954px;top:920px;width:133px">Cum sociis natoque penatibus et magnis dis parturient montes</p>
  <div class="abs meta" style="left:862px;top:994px;gap:9px"><span><i>&#9632;</i> Admin</span><span><i>&#9632;</i> November 03, 2015</span><span><i>&#9679;</i> 14</span></div>
  <div class="abs sep" style="left:862px;top:1023px;width:225px"></div>

  <div class="abs thumb" style="left:862px;top:1041px;width:84px;height:57px;background:linear-gradient(135deg,#d7dee6,#4e5d6e)" role="img" aria-label="Business colleagues at a desk"></div>
  <p class="abs tr-text" style="left:954px;top:1040px;width:133px">Lorem ipsum dolor sit amet, consectetur adipi scing elit.</p>
  <div class="abs meta" style="left:862px;top:1114px;gap:9px"><span><i>&#9632;</i> Admin</span><span><i>&#9632;</i> November 03, 2015</span><span><i>&#9679;</i> 14</span></div>
  <div class="abs sep" style="left:862px;top:1143px;width:225px"></div>

  <div class="abs thumb" style="left:862px;top:1161px;width:84px;height:57px;background:linear-gradient(135deg,#f0f0f0,#7a8796)" role="img" aria-label="Businessman in a suit"></div>
  <p class="abs tr-text" style="left:954px;top:1160px;width:133px">Aenean a est eget dolor mattis laoreet vel eu ipsum. In blandit.</p>
  <div class="abs meta" style="left:862px;top:1234px;gap:9px"><span><i>&#9632;</i> Admin</span><span><i>&#9632;</i> November 03, 2015</span><span><i>&#9679;</i> 14</span></div>
  <div class="abs sep" style="left:862px;top:1263px;width:225px"></div>

  <div class="abs" style="left:862px;top:1300px;width:225px;height:187px;border:2px solid #8a3a08;background:linear-gradient(135deg,#ffb43a,#f07a10 60%,#c85208)" role="img" aria-label="Web hosting advertisement with feature list and get started button"></div>

  <h3 class="abs heading side-title" style="left:862px;top:1513px">Chatterline</h3>
  <div class="abs side-rule" style="left:862px;top:1540px;width:225px"></div>

  <div class="abs tweet-ico" style="left:862px;top:1570px"></div>
  <div class="abs tweet" style="left:917px;top:1563px;width:170px"><h5>14 Oct 2015</h5><p>Typi non habent claritatem in sitam; est usus...</p></div>
  <div class="abs tweet-ico" style="left:862px;top:1639px"></div>
  <div class="abs tweet" style="left:917px;top:1632px;width:170px"><h5>14 Oct 2015</h5><p>Quisque convallis justo aliquam velit molestie...</p></div>
  <div class="abs tweet-ico" style="left:862px;top:1708px"></div>
  <div class="abs tweet" style="left:917px;top:1701px;width:170px"><h5>14 Oct 2015</h5><p>Interdum et malesuada fames ac ante ipsum primis..</p></div>

  <footer class="abs footer"></footer>
  <h3 class="abs heading f-title" style="left:120px">Comments</h3>
  <div class="abs f-rule" style="left:120px"></div>
  <h3 class="abs heading f-title" style="left:371px">Latest News</h3>
  <div class="abs f-rule" style="left:371px"></div>
  <h3 class="abs heading f-title" style="left:621px">Quick Links</h3>
  <div class="abs f-rule" style="left:621px"></div>
  <h3 class="abs heading f-title" style="left:872px">Newsletter Signup</h3>
  <div class="abs f-rule" style="left:872px"></div>

  <div class="abs" style="left:122px;top:1882px;width:84px;height:57px;background:linear-gradient(135deg,#d5dde6,#6d7c8c)" role="img" aria-label="Event audience"></div>
  <div class="abs f-small" style="left:212px;top:1880px;width:135px"><span style="color:#eee"><span style="color:var(--red)">&#9679;</span> 14</span><br>Nulla eget leo posuere, iaculis orci quis,</div>
  <div class="abs" style="left:122px;top:1960px;width:224px;height:1px;background:#3a3a3a"></div>
  <div class="abs" style="left:122px;top:1977px;width:84px;height:57px;background:linear-gradient(135deg,#e7ecf1,#8194a8)" role="img" aria-label="Person typing on a laptop"></div>
  <div class="abs f-small" style="left:212px;top:1975px;width:135px"><span style="color:#eee"><span style="color:var(--red)">&#9679;</span> 14</span><br>Vivamus urna felis, semper vel mi quis</div>
  <div class="abs" style="left:122px;top:2053px;width:224px;height:1px;background:#3a3a3a"></div>

  <div class="abs" style="left:371px;top:1876px;width:226px">
    <div class="f-date"><i>&#9632;</i> November 03, 2015</div>
    <p class="f-small" style="margin-top:4px">Sed ac eros faucibus, porta quam a, aliquam velit. Quisque iaculis elit</p>
    <div style="height:1px;background:#3a3a3a;margin:12px 0 14px"></div>
    <div class="f-date"><i>&#9632;</i> November 03, 2015</div>
    <p class="f-small" style="margin-top:4px">Praesent congue tincidunt aliquam. Mauris vitae ligula ut eros ultricies</p>
    <div style="height:1px;background:#3a3a3a;margin-top:12px"></div>
  </div>

  <div class="abs f-links" style="left:621px;top:1875px"><i>&raquo;</i> Home<br><i>&raquo;</i> Events<br><i>&raquo;</i> Upcoming<br><i>&raquo;</i> Latest Events<br><i>&raquo;</i> Contact Us</div>
  <div class="abs f-links" style="left:747px;top:1875px"><i>&raquo;</i> Politics<br><i>&raquo;</i> International<br><i>&raquo;</i> Privacy Policy<br><i>&raquo;</i> Sitemap</div>

  <p class="abs f-small" style="left:872px;top:1879px;width:226px;line-height:24px">Lorem ipsum dolor sit amet, consectetur adipiscing elit.</p>
  <div class="abs email">Email Address</div>
  <div class="abs subscribe">SUBSCRIBE</div>

  <div class="abs bottom">
    <p>Copyrights@2015 Quellmar Events. All Rights Reserved.</p>
    <div class="abs social" style="left:980px;top:29px;gap:8px"><i class="s1" style="width:22px;height:22px"></i><i class="s2" style="width:22px;height:22px"></i><i class="s3" style="width:22px;height:22px"></i><i class="s4" style="width:22px;height:22px"></i></div>
  </div>

</div>
</body>
</html>
```